Professional Photography Business cards

I need business cards that include my logo which I have uploaded. I run a photography business. I am open to ideas but I would like one side to have my logo and the other side to have my contact info. I don't have a website made but I do own a website domain. I have uploaded 2 different logo color schemes. My business colors are Blue, black , and white.

Business Name
Business Phone Number
Business Email
Business Website address
Instagram

Industry/Entity Type

Professional Photography

Contact Information for Business Card

Phone Number: 916-384-7702 email: info@tlane-studio.example Instagram: @t.lanestudio website doman- www.tlane-studio.example

Requirements
Must have
• I like the idea of a business card with a full black background front and back of card. My colors must include royal blue, black, and white

```html
<!DOCTYPE html>
<html lang="en">
<head>
<meta charset="UTF-8">
<title>T. Lane Studio — Business Card</title>
<link href="https://fonts.googleapis.com/css2?family=Roboto:wght@400&display=swap" rel="stylesheet">
<style>
  :root {
    --royal-blue: #0010a5;
    --card-black: #000000;
    --ink-white: #ffffff;
    --page-bg: #ecebea;
    --disc-light: #f7f5f5;
    --disc-shade: #d3cccc;
  }
  * { box-sizing: border-box; margin: 0; padding: 0; }
  html, body {
    width: 1200px;
    height: 900px;
    overflow: hidden;
    background: var(--page-bg);
  }
  .canvas {
    position: relative;
    width: 1200px;
    height: 900px;
  }
  .business-card {
    position: absolute;
    left: 100px;
    top: 141px;
    width: 1000px;
    height: 618px;
    background: var(--royal-blue);
    overflow: hidden;
    font-family: "Roboto", Arial, sans-serif;
    color: var(--ink-white);
  }
  .black-panel {
    position: absolute;
    top: 0;
    right: 0;
    width: 275px;
    height: 100%;
    background: var(--card-black);
  }
  .brand-disc {
    position: absolute;
    left: 473px;
    top: 56px;
    width: 504px;
    height: 504px;
    border-radius: 50%;
    background: radial-gradient(circle at 45% 35%, var(--disc-light) 0%, #ece8e8 55%, var(--disc-shade) 100%);
    display: flex;
    align-items: center;
    justify-content: center;
    gap: 16px;
  }
  .brand-mark {
    width: 30px;
    height: 30px;
    border-radius: 50%;
    background: var(--royal-blue);
  }
  .brand-name {
    font-family: "Roboto", Arial, sans-serif;
    font-weight: 400;
    font-size: 46px;
    letter-spacing: 1px;
    color: var(--royal-blue);
  }
  .contact-list {
    position: absolute;
    left: 50px;
    top: 70px;
    list-style: none;
  }
  .contact-item {
    display: flex;
    align-items: center;
    height: 37px;
    font-size: 28px;
    line-height: 1;
  }
  .contact-icon {
    width: 28px;
    height: 28px;
    margin-right: 10px;
    flex: none;
  }
  .social-handle {
    position: absolute;
    left: 50px;
    top: 511px;
    display: flex;
    align-items: center;
    font-size: 28px;
  }
  .social-square {
    width: 30px;
    height: 30px;
    border: 3px solid var(--ink-white);
    border-radius: 6px;
    margin-right: 8px;
  }
</style>
</head>
<body>
<div class="canvas">
  <section class="business-card">
    <div class="black-panel"></div>

    <ul class="contact-list">
      <li class="contact-item">
        <svg class="contact-icon" viewBox="0 0 24 24" fill="none" stroke="currentColor" stroke-width="2" stroke-linecap="round" stroke-linejoin="round" aria-hidden="true">
          <path d="M22 16.9v3a2 2 0 0 1-2.2 2 19.8 19.8 0 0 1-8.6-3.1 19.5 19.5 0 0 1-6-6A19.8 19.8 0 0 1 2.1 4.2 2 2 0 0 1 4.1 2h3a2 2 0 0 1 2 1.7c.1 1 .4 1.9.7 2.8a2 2 0 0 1-.5 2.1L8 9.9a16 16 0 0 0 6 6l1.3-1.3a2 2 0 0 1 2.1-.4c.9.3 1.8.6 2.8.7a2 2 0 0 1 1.8 2z"/>
          <path d="M15 2.5a7 7 0 0 1 6.5 6.5M15 6a3.5 3.5 0 0 1 3 3"/>
        </svg>
        <span>916-384-7702</span>
      </li>
      <li class="contact-item">
        <svg class="contact-icon" viewBox="0 0 24 24" aria-hidden="true">
          <rect x="1.5" y="5" width="21" height="14" fill="currentColor"/>
          <path d="M1.5 5l10.5 8 10.5-8M1.5 19l8-7M22.5 19l-8-7" fill="none" stroke="var(--royal-blue)" stroke-width="1.6"/>
        </svg>
        <span>info@tlane-studio.example</span>
      </li>
      <li class="contact-item">
        <svg class="contact-icon" viewBox="0 0 24 24" fill="none" stroke="currentColor" stroke-width="1.8" aria-hidden="true">
          <circle cx="12" cy="12" r="10"/>
          <path d="M2 12h20M12 2c3 3 3 17 0 20M12 2c-3 3-3 17 0 20M4 6.5h16M4 17.5h16"/>
        </svg>
        <span>www.tlane-studio.example</span>
      </li>
    </ul>

    <div class="social-handle">
      <span class="social-square" aria-hidden="true"></span>
      <span>@t.lanestudio</span>
    </div>

    <div class="brand-disc">
      <span class="brand-mark" aria-hidden="true"></span>
      <span class="brand-name">T. Lane Studio</span>
    </div>
  </section>
</div>
</body>
</html>
```